Zielgruppe
Ich biete farbtupferei, Glitzertattoos, Schwangerschaftsbemalung (Belly-Painting), Wunden schminken, Vermietung von einer Popcornmaschine.
Aufgabenstellung
Mein Anliegen betrifft hiermit die Gestaltung einer Website.
In Bezug auf die Website gibt es schon eine gekaufte Domain, welche lautet: frau-pinselmaus.de und kann über VERAX eingerichtet werden.
Auf dieser WEBSITE soll sich folgendes Menü befinden:
- Anfrage stellen/Angebot einholen mit zusätzlicher Frage 'Wie sind Sie auf mich aufmerksam geworden?'
Mit einem Feld für den Namen, E-Mail, Telefonnummer, Gewünschtes Datum.
Sowie die Frage 'Wie sind Sie auf mich aufmerksam geworden?' (zum Ankreuzen) Freunde, Empfehlung, Flyer, soziale medienoder sonstiges.
Gerne auch zum ankreuzen welche Leistung Sie möchten. farbtupferei, Glitzer Tattoos, Schwangerschaftsbemalung, oder Popcornmaschiene. (So brauchen haben es die Kunden einfacher nur anzukreuzen und ich sehe gleich worum es sich handelt.)
- eine Leistungsübersicht: farbtupferei, Glitzertattoos, Schwangerschaftsbemalung (Belly-Painting), Wunden schminken, Vermietung von einer Popcornmaschine
- meine Kontaktdaten
- Galerie (es kann eine Auswahl der angehängten Bilder sein)
!!! mein Wunsch wäre, dass sich die Figur von dem Logo in verschiedenen Positionen auf der Website an das Menü angepasst wiederfindet (wenn dies irgendwie machbar ist)
z.B. meine Figur (Logo) stehend am Rand oder liegend.....
- erwünscht ist auch eine Verknüpfung mit einem Findlaeintrag
- Hinweis auf Kontaktor und Lumoravue (bin gerade dabei ein öffentliches Profil dort zu erstellen)
!Wichtig wäre die nötige Einstellung, damit die Website sowohl in der mobilen Version als auch der PC-Version mit ALLEN oben genannten Informationen dargestellt wird!
Dankbar wäre ich noch für die Information, ob für mich laufende Kosten (monatlich oder jährlich) für die Website entstehen?
Mein Logo ist mir sehr wichtig und sollte gut sichtbar und erkennbar sein auch die Schriftart kann auf der Website aufgegriffen werden

```html
<!DOCTYPE html>
<html lang="de">
<head>
<meta charset="utf-8">
<title>Frau Pinselmaus – Farbtupferei & Glitzer Tattoos</title>
<link rel="stylesheet" href="https://fonts.googleapis.com/css2?family=Poppins:wght@400;500;600;700;800&display=swap">
<style>
:root{
  --teal:#1a9bab;
  --teal-dark:#158c9b;
  --sky-0:#ffffff;
  --sky-1:#eef8fa;
  --sky-2:#bfe4ea;
  --sky-3:#7fcad4;
  --sky-4:#3aaebd;
  --orange:#f08646;
  --ink:#222;
  --white:#ffffff;
}
*{box-sizing:border-box;margin:0;padding:0}
html,body{width:1200px;height:4820px;overflow:hidden}
body{font-family:"Poppins",sans-serif;color:var(--ink);position:relative;
  background:linear-gradient(180deg,var(--sky-0) 0px,var(--sky-1) 1100px,#e4f3f6 2200px,var(--sky-2) 2450px,var(--sky-3) 3500px,var(--sky-4) 4517px,var(--white) 4517px)}
.abs{position:absolute}
.brand{display:flex;align-items:center;gap:12px;color:var(--teal);font-weight:600;font-size:28px;line-height:1.1}
.brand .dot{width:30px;height:30px;border-radius:50%;background:var(--teal);flex:none}
.nav a{position:absolute;top:80px;font-size:22px;color:var(--teal);text-decoration:none;font-weight:400;letter-spacing:.5px}
.nav a.active{font-weight:700}
.heading{font-weight:800;font-size:94px;line-height:1;letter-spacing:-1px}
.heading.teal{color:var(--teal)}
.heading.white{color:var(--white);text-align:center;width:1200px;left:0}
.service-photo{position:absolute;width:272px;height:272px;border-radius:50%}
.service-label{position:absolute;font-weight:600;font-size:29px;text-align:center;width:320px;line-height:42px;color:#111}
.gallery{position:absolute;left:45px;top:1295px;width:1110px;height:993px;display:grid;grid-template-columns:repeat(3,1fr);grid-template-rows:repeat(3,1fr);gap:4px}
.gallery div{width:100%;height:100%}
.review{position:absolute;border:3px solid var(--orange);border-radius:4px;text-align:center;font-size:18px;line-height:28px;color:#222;padding:12px 24px}
.review .stars{color:var(--white);font-size:22px;letter-spacing:2px;line-height:26px;margin-bottom:10px}
.palette{position:absolute;width:94px;height:94px;border-radius:50%;background:#e9f5f7;border:3px solid #222}
.field{position:absolute;left:256px;width:710px;border:2px solid var(--white);background:rgba(255,255,255,.18);color:var(--white);font-size:29px;padding:0 10px;line-height:44px}
.question{position:absolute;left:262px;color:var(--white);font-size:29px}
.check{position:absolute;color:var(--white);font-size:29px;display:flex;align-items:center;gap:14px}
.check i{display:block;width:36px;height:36px;border:2px solid var(--white);border-radius:5px}
.submit{position:absolute;left:256px;top:4349px;width:710px;height:50px;background:var(--orange);color:var(--white);font-size:29px;text-align:center;line-height:50px}
.contact{position:absolute;right:19px;top:4570px;text-align:right;color:var(--teal);font-size:29px;line-height:42px}
.social{position:absolute;top:4716px;width:48px;height:48px;border-radius:6px;background:var(--teal)}
</style>
</head>
<body>

<header>
  <div class="brand abs" style="left:26px;top:74px"><span class="dot"></span>Frau Pinselmaus</div>
  <nav class="nav">
    <a style="left:324px">LEISTUNGEN</a>
    <a style="left:575px">GALERIE</a>
    <a style="left:781px">REFERENZEN</a>
    <a class="active" style="left:1031px">KONTAKT</a>
  </nav>
</header>

<section class="services">
  <h2 class="heading teal abs" style="left:20px;top:240px">LEISTUNGEN</h2>
  <div class="service-label" style="left:10px;top:418px">Belly Painting</div>
  <div class="service-label" style="left:448px;top:414px">Glitzertattoos</div>
  <div class="service-label" style="left:885px;top:414px">Farbtupferei</div>
  <div class="service-photo" role="img" aria-label="Bemalter Babybauch" style="left:36px;top:482px;background:radial-gradient(circle,#9a9a9a,#5e4a40)"></div>
  <div class="service-photo" role="img" aria-label="Glitzertattoos auf einem Arm" style="left:478px;top:482px;background:radial-gradient(circle,#b89a86,#5a4a40)"></div>
  <div class="service-photo" role="img" aria-label="Farbtupferei beim Schminken" style="left:907px;top:467px;background:radial-gradient(circle,#6a86b8,#2a2a32)"></div>
  <div class="service-photo" role="img" aria-label="Geschminkte Wunde" style="left:242px;top:688px;background:radial-gradient(circle,#a43040,#e8d8d0)"></div>
  <div class="service-photo" role="img" aria-label="Popcorntüten" style="left:699px;top:688px;background:radial-gradient(circle,#f4e6e0,#c8443c)"></div>
  <div class="service-label" style="left:214px;top:970px">Wunden<br>Schminken</div>
  <div class="service-label" style="left:692px;top:970px">Verleih<br>Popcornmaschine</div>
</section>

<section>
  <h2 class="heading teal abs" style="right:48px;top:1140px">GALERIE</h2>
  <div class="gallery">
    <div role="img" aria-label="Belly Painting im Freien" style="background:linear-gradient(160deg,#3f5a2e,#7a8a5a)"></div>
    <div role="img" aria-label="Glitzertattoo wird aufgetragen" style="background:linear-gradient(160deg,#d8b8c4,#8a6a66)"></div>
    <div role="img" aria-label="Bodypainting mit Motiv" style="background:linear-gradient(160deg,#8a5a3c,#3a7ab4)"></div>
    <div role="img" aria-label="Gruppe mit Glitzertattoos" style="background:linear-gradient(160deg,#8a8070,#4a6a30)"></div>
    <div role="img" aria-label="Glitzertattoo am Arm" style="background:linear-gradient(160deg,#e0b0c8,#b88a8c)"></div>
    <div role="img" aria-label="Bemalte Hand" style="background:linear-gradient(160deg,#2a2a30,#1c1c22)"></div>
    <div role="img" aria-label="Schminken eines Kindes" style="background:linear-gradient(160deg,#8a6a58,#2a2a30)"></div>
    <div role="img" aria-label="Bodypainting in Arbeit" style="background:linear-gradient(160deg,#8a6a40,#2a4a6a)"></div>
    <div role="img" aria-label="Bienenmotiv auf Wange" style="background:linear-gradient(160deg,#d89a70,#e8c8a8)"></div>
  </div>
</section>

<section>
  <h2 class="heading white abs" style="top:2412px">REFERENZEN</h2>
  <div class="review" style="left:86px;top:2550px;width:492px;height:112px"><div class="stars">★★★★★</div>Alles Bestens, würde ich wieder buchen!</div>
  <div class="review" style="left:610px;top:2550px;width:493px;height:112px"><div class="stars">★★★★★</div>Ich kann nichts sagen außer, super!</div>
  <div class="review" style="left:86px;top:2679px;width:490px;height:200px"><div class="stars">★★★★★</div>So freundlich zu den kleinen. Habe Sie zu einem Kindergeburtstag meiner Tochter gebucht und diese war begeistert. Wirklich zu empfehlen.</div>
  <div class="review" style="left:610px;top:2679px;width:489px;height:200px"><div class="stars">★★★★★</div>Die Kids sind super auf die Popcornmaschine abgefahren.<br>War der Hit der Feier!</div>
  <div class="palette" role="img" aria-label="Farbpalette" style="left:1052px;top:2499px"></div>
  <div class="palette" role="img" aria-label="Farbpalette" style="left:50px;top:2826px"></div>
</section>

<section>
  <h2 class="heading white abs" style="top:2958px">INTERESSE GEWECKT?</h2>
  <h2 class="heading white abs" style="top:3100px">KONTAKT</h2>
  <div class="field" style="top:3261px;height:50px">Name</div>
  <div class="field" style="top:3336px;height:50px">E-Mail Adresse</div>
  <div class="field" style="top:3418px;height:51px">Gewünschtes Datum</div>
  <div class="question" style="top:3494px">Welche Leistung wollen Sie in Anspruch nehmen?</div>
  <div class="check" style="left:256px;top:3546px"><i></i>Farbtupferei</div>
  <div class="check" style="left:256px;top:3597px"><i></i>Glitzertattoos</div>
  <div class="check" style="left:256px;top:3651px"><i></i>Popcornmaschine mieten</div>
  <div class="check" style="left:256px;top:3711px"><i></i>Sonstiges</div>
  <div class="question" style="top:3765px">Wie sind Sie auf mich aufmerksam geworden?</div>
  <div class="check" style="left:256px;top:3818px"><i></i>Freunde</div>
  <div class="check" style="left:457px;top:3818px"><i></i>Sozial Media</div>
  <div class="check" style="left:709px;top:3818px"><i></i>Empfehlung</div>
  <div class="check" style="left:256px;top:3874px"><i></i>Sonstiges</div>
  <div class="field" style="top:3957px;height:358px">Ihre Nachricht</div>
  <div class="submit">Absenden</div>
</section>

<footer>
  <div class="brand abs" style="left:37px;top:4650px"><span class="dot"></span>Frau Pinselmaus</div>
  <div class="contact">Mira Musterfrau<br>Telefon: 0123 456789012<br>Email: hallo@beispielpost.de</div>
  <div class="social" role="img" aria-label="Kontaktor" style="left:1071px"></div>
  <div class="social" role="img" aria-label="Lumoravue" style="left:1135px"></div>
</footer>

</body>
</html>
```